Law Firm Web Design Project

I need a website design for my law firm. I have attached to this description the URL of a website I liked with a description of the elements of that website that appeal to me.

I am also attaching my law firm's logo, so you can review that design when you create the website design.

Reference Site: www.harborfieldcounsel-example.com

What we like about this site:
• The different layers
• Subtle designs, textures, curves
• 3 dimensional
• Floating effect
• Simple logo that stands out (we are providing logo)
• Prominent phone number
• Location of Areas of Practice
oDivorce, Legal Separation, Paternity, Spousal Maintenance, Child Custody, Child Support, Protective Orders, Community Property, Business Evaluations
• The limited amount of links across the top
o Home, Meet Our Attorney, FAQ, Contact Us
• Request A Consultation click through
• Right side bar with the moving icons
• Badges

Other Tips:
• We don’t want the website to be dark. The logo can standout and the website can have its own colors and flow.
• We would like there to be a “call to action” or way to get in touch on every page and every page view
• We would like a place for credit card icons at the bottom of the page
• Strong, yet elegant
• Finally, just use the website provided as a guide. Explore different colors, textures, shapes, shadows etc.
Updates

I would prefer the website have colors that are complementary to my logo and that are strong and elegant.  I like black, gold, amber, and tan colors.  Black should be used sparingly as an accent only, since I don't want the website to be too dark.

Please review the website I provided as an example in my project description.  I really like the three dimensional aspects of that website (web page floating on top of a background and the logo in the upper left floating on top of the web page).  I also like the use of "swirling" on the background and the webpage.  I hope this additional information is helpful.

Requirements
Must have
• I need a place to insert "client testimonials", a place to insert four logos of awards the law firm has received, a place for people to fill out a form to contact the law firm via email, and a place for people to click to review articles I have written.

```html
<!DOCTYPE html>
<html lang="en">
<head>
<meta charset="utf-8">
<title>Marlowe Law</title>
<link rel="stylesheet" href="https://fonts.googleapis.com/css2?family=Open+Sans:wght@400;600;700&family=Marcellus&family=Arimo:wght@400;700&family=Arvo:wght@700&display=swap">
<style>
:root{
  --page-bg:#000;
  --white:#fff;
  --gold:#8c7630;
  --gold-dark:#6b5a1f;
  --gold-light:#efe3bf;
  --tan:#e5dfc9;
  --panel:#f0ede3;
  --text:#7a7a7a;
  --heading:#7a5f14;
  --footer:#a08d47;
  --footer-text:#f3eedd;
  --amber:#f2a51d;
  --yellow:#ffe000;
  --link:#1b4fd6;
}
*{margin:0;padding:0;box-sizing:border-box}
html,body{width:959px;height:1200px;overflow:hidden;background:var(--page-bg)}
.page{position:absolute;left:87px;top:0;width:785px;height:1200px;background:var(--tan)}
.header{position:absolute;left:0;top:0;width:785px;height:133px;background:var(--white);border-bottom:3px solid #c9b679;overflow:hidden}
.header-swoosh{position:absolute;left:0;top:0}
.brand{position:absolute;left:14px;top:32px;display:flex;align-items:center;gap:14px}
.brand-mark{width:52px;height:52px;background:#1a1a1a}
.brand-name{font-family:"Marcellus",serif;font-size:38px;color:var(--gold);letter-spacing:1px}
.phone-line{position:absolute;right:12px;top:8px;font-family:"Arimo",sans-serif;font-weight:700;font-size:15px;color:#6b5413}
.phone-line b{color:#3a2d08;font-size:16px;margin-left:6px}
.nav{position:absolute;right:0;top:106px;display:flex;font-family:"Open Sans",sans-serif;font-size:12px;color:#222}
.nav a{color:inherit;text-decoration:none;padding:4px 11px 5px;margin-left:18px}
.nav a.active{background:#a88d3c;color:#fff;font-weight:600;border-radius:3px 3px 0 0}
.hero{position:absolute;left:0;top:135px;width:785px;height:228px;background:linear-gradient(90deg,#b8b0ad 0%,#7a6e69 30%,#4d4744 60%,#3f3a38 100%);}
.hero-glow{position:absolute;left:0;bottom:0;width:785px;height:90px;background:linear-gradient(180deg,rgba(120,70,30,0) 0%,rgba(110,60,25,.55) 100%)}
.cta{position:absolute;left:536px;top:296px;width:240px;height:56px;border-radius:28px;background:linear-gradient(180deg,#ffd05a 0%,#f4a51b 55%,#e08c0c 100%);box-shadow:0 2px 4px rgba(0,0,0,.4);font-family:"Open Sans",sans-serif;font-style:italic;font-weight:700;font-size:18px;color:#fff;display:flex;align-items:center;padding-left:20px;text-decoration:none}
.cta svg{position:absolute;right:14px;top:14px}
.intro{position:absolute;left:1px;top:383px;width:510px;height:432px;background:var(--panel);border-radius:0 36px 36px 0;padding:18px 26px 0 20px}
.intro h1{font-family:"Open Sans",sans-serif;font-weight:600;font-size:16px;color:var(--heading);margin-bottom:18px}
.intro h2{font-family:"Open Sans",sans-serif;font-weight:400;font-size:14px;color:#111;margin-bottom:5px}
.intro p{font-family:"Arimo",sans-serif;font-size:11.6px;line-height:15.6px;color:var(--text);text-align:justify;margin-bottom:15px}
.testimonial{position:absolute;left:533px;top:393px;width:228px;height:220px;background:var(--yellow);transform:rotate(2deg);box-shadow:2px 3px 4px rgba(0,0,0,.25);padding:30px 16px 0 22px;font-family:"Arimo",sans-serif}
.testimonial h3{font-family:"Arvo",serif;font-size:17px;color:#111;margin-bottom:10px}
.testimonial p{font-size:10.4px;line-height:14.5px;color:#111}
.testimonial .author{margin-top:14px;font-weight:700;font-size:10.4px;line-height:14px}
.contact-card{position:absolute;left:531px;top:645px;width:230px;height:166px;background:var(--white);border-radius:6px;text-align:center;font-family:"Open Sans",sans-serif}
.contact-card svg{position:absolute;left:12px;top:12px}
.contact-card h3{position:absolute;left:82px;top:20px;font-weight:400;font-size:17px;color:#7a5a0c}
.contact-card .help{position:absolute;left:0;top:76px;width:100%;font-size:13px;line-height:18px;color:#7a5a0c}
.contact-card .cta-link{position:absolute;left:0;top:115px;width:100%;font-size:10.5px;line-height:14px;color:#6b5413;font-weight:600}
.contact-card .cta-link a{color:var(--link);text-decoration:underline}
.badge{position:absolute;top:837px;height:168px;background:var(--white);border-radius:6px;display:flex;align-items:center;justify-content:center}
.badge-shape{background:#d9d2bb}
.footer{position:absolute;left:0;top:1030px;width:785px;height:170px;background:var(--footer);font-family:"Open Sans",sans-serif;color:var(--footer-text)}
.footer-links{position:absolute;left:14px;top:16px;font-size:12px;font-weight:600;color:#fff}
.disclaimer{position:absolute;left:14px;top:44px;width:360px;font-size:10px;line-height:16.5px}
.footer-contact-title{position:absolute;left:472px;top:16px;font-size:12px;font-weight:700;color:#fff}
.footer-address{position:absolute;left:472px;top:42px;font-size:9.5px;line-height:18px}
.footer-phones{position:absolute;left:600px;top:42px;font-family:"Arimo",sans-serif;font-size:10.5px;line-height:18px}
.cards{position:absolute;left:16px;top:131px;width:168px;height:28px;background:#fff;display:flex;gap:3px;padding:3px}
.card{flex:1;border:1px solid #bbb;font-family:"Open Sans",sans-serif;font-size:7.5px;font-weight:700;color:#444;display:flex;align-items:center;justify-content:center}
.copyright{position:absolute;left:471px;top:148px;font-family:"Arimo",sans-serif;font-size:11px}
</style>
</head>
<body>
<div class="page">
  <header class="header">
    <svg class="header-swoosh" width="785" height="133" viewBox="0 0 785 133" aria-hidden="true">
      <defs>
        <linearGradient id="swooshFill" x1="0" y1="0" x2="1" y2="0">
          <stop offset="0" stop-color="#e9dcb3"/>
          <stop offset="1" stop-color="#f4ead0"/>
        </linearGradient>
      </defs>
      <path d="M340 0 C320 40 340 95 430 115 C520 130 650 128 785 126 L785 0 Z" fill="url(#swooshFill)"/>
      <path d="M340 0 C320 40 340 95 430 115 C520 130 650 128 785 126" fill="none" stroke="#a88d3c" stroke-width="7"/>
      <line x1="0" y1="130" x2="785" y2="130" stroke="#a88d3c" stroke-width="3"/>
    </svg>
    <div class="brand">
      <div class="brand-mark"></div>
      <div class="brand-name">Marlowe Law</div>
    </div>
    <div class="phone-line">Call us on <b>555 010 4477</b></div>
    <nav class="nav">
      <a class="active" href="#">Home</a>
      <a href="#">Meet Our Attorney</a>
      <a href="#">FAQ</a>
      <a href="#">Contact Us</a>
    </nav>
  </header>

  <div class="hero" role="img" aria-label="Photo of a wooden judge's gavel resting on a polished desk">
    <div class="hero-glow"></div>
  </div>
  <a class="cta" href="#">CALL TO ACTION
    <svg width="28" height="28" viewBox="0 0 28 28" aria-hidden="true">
      <circle cx="14" cy="14" r="13" fill="#fff3c9" stroke="#e29514" stroke-width="1.5"/>
      <path d="M11 8 L19 14 L11 20 Z" fill="#e8960f"/>
    </svg>
  </a>

  <section class="intro">
    <h1>Marlowe Divorce Lawyer</h1>
    <h2>Help with Your Divorce and Family Law Matters</h2>
    <p>Aenean in turpis lorem, eget dignissim mi. Duis nulla lorem, pharetra quis tempor a, blandit id risus. Quisque augue dui, vulputate vitae rutrum vitae, porta nec tortor. Class aptent taciti sociosqu ad litora torquent per conubia nostra, per inceptos himenaeos. Ut a sapien metus, vitae tempus tortor. Donec malesuada, tellus a rhoncus ultricies, ligula mauris semper turpis, a egestas sapien nisi et metus. Curabitur et nisi turpis, volutpat hendrerit est. In vel magna odio, non egestas sem. Cras suscipit purus sed tortor cursus tincidunt. Nunc sodales nisl consectetur elit consectetur condimentum. Morbi mi mauris, vehicula gravida suscipit ac, pulvinar sit amet metus. Phasellus nibh ipsum, sollicitudin vel fermentum ut, porttitor eu tortor. Aliquam erat volutpat. Curabitur eget sapien quis turpis lobortis venenatis. Suspendisse porta metus at velit rutrum tincidunt eu sit amet est.</p>
    <p>Pellentesque habitant morbi tristique senectus et netus et malesuada fames ac turpis egestas. Pellentesque quam lorem, ultrices in eleifend in, dictum at neque. Nam vulputate velit non velit malesuada bibendum interdum lectus congue. Morbi ullamcorper adipiscing tellus, eu varius neque lacinia nec. Integer interdum, risus a dapibus pretium, risus urna accumsan tellus, sed posuere lacus est sit amet leo. Vivamus vitae elit faucibus nisi ornare cursus. Integer et risus tortor. Proin nec pulvinar quam. Suspendisse ac dui tortor. Duis diam lectus, ornare sed placerat a, tempus ac mi. Pellentesque iaculis ultricies nunc in tristique. In suscipit, libero at viverra lacinia, lectus risus vehicula tellus, sit amet consequat enim orci at eros. Nullam aliquet magna vitae libero ornare viverra.</p>
  </section>

  <aside class="testimonial">
    <h3>Client Testimonials</h3>
    <p>Lorem ipsum dolor sit amet, consectetur adipiscing elit. Curabitur consectetur rutrum dignissim. Nunc accumsan lacinia nisi nec iaculis. Etiam id nisi vel est volutpat rhoncus. Donec condimentum auctor nisi, eu mollis tellus rhoncus in.</p>
    <div class="author">Jordan,<br>MarloweLaw.net</div>
  </aside>

  <aside class="contact-card">
    <svg width="56" height="40" viewBox="0 0 56 40" aria-hidden="true">
      <path d="M4 10 C4 3 52 3 52 10 L52 15 L42 15 L42 10 L14 10 L14 15 L4 15 Z" fill="#1e1e1e"/>
      <path d="M16 14 L40 14 L48 36 L8 36 Z" fill="#2a2a2a"/>
      <circle cx="28" cy="25" r="6" fill="#777"/>
      <circle cx="28" cy="25" r="2.5" fill="#1e1e1e"/>
    </svg>
    <h3>CONTACT US</h3>
    <div class="help">For help in divorce &amp;<br>other family law matters</div>
    <div class="cta-link"><a href="#">Contact a Marlowe divorce attorney</a><br>for caring legal assistance.</div>
  </aside>

  <div class="badge" style="left:9px;width:289px"><div class="badge-shape" style="width:250px;height:110px;border-radius:4px"></div></div>
  <div class="badge" style="left:320px;width:290px"><div class="badge-shape" style="width:220px;height:130px;border-radius:4px"></div></div>
  <div class="badge" style="left:632px;width:146px"><div class="badge-shape" style="width:100px;height:160px;border-radius:6px;background:#1f5f7a"></div></div>

  <footer class="footer">
    <div class="footer-links">Marlowe Divorce Attorney | Contact Us | Resources | Privacy Policy | Site Map</div>
    <p class="disclaimer">The information on this website is for general information purposes only. Nothing on this site should be taken as legal advice for any individual case or situation. This information is not intended to create, and receipt or viewing does not constitute, an attorney-client relationship.</p>
    <div class="footer-contact-title">Contact Us</div>
    <div class="footer-address">Dana Holt<br>Unit 4 Orchard Lane,<br>Bramford, SA, 5170<br>PO Box 212,<br>Bramford, SA, 5170</div>
    <div class="footer-phones">Phone Work/Mobile: 0400555123<br>Phone: 08 5550 1234<br>Fax: 08 55501299<br>Email: dana@orchardfieldmail.com</div>
    <div class="cards">
      <div class="card">Crestpay</div>
      <div class="card">Nova</div>
      <div class="card">Meridian</div>
      <div class="card">Orbit</div>
    </div>
    <div class="copyright">© 2012 Marlowe. All Rights Reserved.</div>
  </footer>
</div>
</body>
</html>
```